Design website home page for pathology consulting company

Starting a new consulting company with anatomic pathologists focused on expert diagnosis and second opinions on difficult pathology cases. In the near future we will be incorporating next generation diagnostics for rare diseases of childhood into the business. These include discovery and testing of DNA for mutations.

The company is formed around one of the best known pathologists in the world named Marcel "Biscuit" Trowell. The name of the company is "BiscuitLab"

We had a logo design by SketchForum - it is great. I will attach file as soon as I have it (contest ending today). Our company is medical, uses microscopes, DNA, probably will focus on childhood diseases but not solely on childhood diseases. we're not particularly conservative, but the customers we want to appeal to include older practicing pathologists as well as patients (sometimes parents) looking for second opinions.

Think a group of expert doctors diagnosing disease through the microscope and through DNA technology, ages ranging from 35-75 all trained by the best pathologist in the world - "Biscuit"

We receive glass slides from diseases from patients all over the world from docs who need an expert to tell them what is the diagnosis. So "path to the diagnosis" is also part of the company marketing message.

We want the website design to describe our company but be very simple to find what one is looking for as we will use it as the launch page to:
1) order services
2) check results/reports
3) set up new account
4) speak with one of the pathologists
5) see our test menu
6) access our educational material/webinars
Updates

Update - looking for home page design and then finalists will ask for second page design to keep with theme - ok?

Reason: realized this project isn't web design but web home page design - thanks

Reason: Holidays for some in next two weeks

Reason: Hot discussion among collaborators for a few of the submissions. Will provide detail individually this weekend. Thanks so much for all the submissions!

Target Market(s)

Referring pathologists, physicians who want second opinions on pathology disease diagnosis, patients who have had biopsies (either patients themselves or parents of patients), generally high education level

Industry/Entity Type

Marketing

Requirements
Must have
• BiscuitLab
Next Generation Pathology Consultants

```html
<!DOCTYPE html>
<html lang="en">
<head>
<meta charset="utf-8">
<title>BiscuitLab – Next Generation Pathology Consultants</title>
<link href="https://fonts.googleapis.com/css2?family=Open+Sans:ital,wght@0,300;0,400;0,600;1,300&family=PT+Sans:wght@400&family=Noto+Serif:ital@1&display=swap" rel="stylesheet">
<style>
  :root {
    --brand-blue: #1a63a8;
    --link-blue: #1f6cb5;
    --text-dark: #222;
    --text-body: #777;
    --text-quote: #b8b8b8;
    --rule: #d2d2d2;
    --rule-dotted: #c8c8c8;
    --footer-bg: #6d6d6d;
    --photo-a: #c9d3dc;
    --photo-b: #4e9fbf;
    --photo-c: #e9ecef;
  }
  * { box-sizing: border-box; margin: 0; padding: 0; }
  html, body { width: 1183px; height: 1200px; overflow: hidden; background: #fff; }
  body { position: relative; font-family: "Open Sans", Arial, sans-serif; color: var(--text-dark); }
  a { color: inherit; text-decoration: none; }

  .brand { position: absolute; left: 98px; top: 10px; width: 162px; text-align: center; }
  .brand-mark { width: 76px; height: 76px; border-radius: 50%; background: linear-gradient(180deg, #d5d5d5, #8d8d8d); margin: 0 auto 2px; }
  .brand-name { font-size: 25px; font-weight: 400; color: var(--brand-blue); letter-spacing: 0.5px; line-height: 28px; }
  .brand-tagline { font-size: 8.5px; color: #666; line-height: 10px; }

  .order-line { position: absolute; right: 97px; top: 34px; font-size: 16px; font-weight: 600; color: var(--brand-blue); }
  .order-line span { color: #333; }

  .main-nav { position: absolute; right: 97px; top: 92px; display: flex; font-size: 12.5px; }
  .main-nav a { padding: 0 19px; border-left: 1px dotted #bbb; line-height: 20px; }
  .main-nav a:first-child { border-left: none; }
  .main-nav a:last-child { padding-right: 0; }
  .main-nav a.current { color: var(--link-blue); }
  .main-nav a.current span { border-bottom: 1px solid var(--link-blue); padding-bottom: 1px; }

  .rule { position: absolute; left: 98px; width: 988px; height: 1px; background: var(--rule); }

  .intro-quote { position: absolute; left: 98px; top: 159px; width: 988px; font-size: 23.5px; font-weight: 300; font-style: italic; color: var(--text-quote); line-height: 34px; }

  .hero { position: absolute; left: 98px; top: 314px; width: 988px; height: 318px; border: 1px solid #ccc;
          background: linear-gradient(100deg, var(--photo-c) 0%, var(--photo-a) 30%, var(--photo-b) 55%, #d9c4b4 75%, var(--photo-c) 100%); }
  .hero-dots { position: absolute; right: 18px; bottom: 18px; display: flex; gap: 7px; }
  .hero-dots i { width: 14px; height: 14px; background: #e8e8e8; display: block; }
  .hero-dots i.active { background: var(--brand-blue); }

  .tabs { position: absolute; left: 97px; top: 659px; width: 727px; height: 31px; border-bottom: 1px solid var(--rule); display: flex; gap: 4px; }
  .tab { height: 31px; padding: 0 12px; line-height: 30px; font-size: 12.5px; border: 1px solid var(--rule); border-bottom: none; border-radius: 3px 3px 0 0; background: #fff; }
  .tab.active { background: var(--brand-blue); border-color: var(--brand-blue); color: #fff; padding: 0 17px; }

  .article { position: absolute; width: 350px; font-family: "PT Sans", Arial, sans-serif; font-size: 12px; letter-spacing: 0.5px; line-height: 18px; color: var(--text-body); }
  .article h2 { font-family: "Open Sans", Arial, sans-serif; font-weight: 400; font-size: 20px; color: var(--link-blue); letter-spacing: 0; line-height: 26px; }
  .article .lead { font-family: "Noto Serif", Georgia, serif; font-style: italic; font-size: 11.5px; color: #333; text-decoration: underline; letter-spacing: 0.8px; line-height: 18px; }
  .article u, .article .inline-link { color: #333; text-decoration: underline; }
  .article .strong-link { color: #555; text-decoration: underline; font-weight: 700; }
  .article .more { color: #333; text-decoration: underline; display: inline-block; }
  .divider-dotted { border-top: 1px dotted var(--rule-dotted); }
  .divider-solid { height: 2px; background: #ddd; }

  .col-left { left: 95px; top: 713px; }
  .col-mid { left: 477px; top: 711px; }
  .article-photo { width: 349px; height: 191px; border-radius: 4px; background: linear-gradient(120deg, #2a3f72 0%, #5b6574 45%, #b9b9ae 75%, #e2e0d6 100%); }

  .sidebar { position: absolute; left: 865px; top: 660px; width: 221px; }
  .sidebar h3 { font-weight: 400; font-size: 20px; color: #555; line-height: 26px; margin-bottom: 13px; }
  .service-list { list-style: none; }
  .service-list li { height: 30px; border-bottom: 1px solid #e3e3e3; display: flex; align-items: center; font-size: 10.5px; color: var(--link-blue); }
  .service-list svg { width: 14px; height: 14px; margin: 0 11px 0 7px; flex: none; }
  .btn { display: flex; align-items: center; justify-content: center; text-align: center; color: #fff; font-size: 17px; line-height: 20px; }
  .btn-dark { margin-top: 13px; height: 39px; background: linear-gradient(180deg, #3a3a3a, #0f0f0f); border: 1px solid #000; }
  .btn-blue { margin-top: 12px; height: 48px; background: linear-gradient(180deg, #2a86d2, #0d5ca7); }

  .site-footer { position: absolute; left: 0; top: 1153px; width: 1183px; height: 47px; background: var(--footer-bg); }
  .copyright { position: absolute; left: 98px; top: 14px; font-size: 11.5px; color: #fff; }
  .social { position: absolute; right: 97px; top: 15px; display: flex; gap: 9px; }
  .social i { width: 17px; height: 17px; border-radius: 3px; display: block; }
</style>
</head>
<body>
  <header>
    <div class="brand">
      <div class="brand-mark"></div>
      <div class="brand-name">BiscuitLab</div>
      <div class="brand-tagline">Next Generation Pathology Consultants</div>
    </div>
    <div class="order-line">24/7 ORDER <span>080-4417-362</span></div>
    <nav class="main-nav">
      <a class="current" href="#"><span>Home</span></a>
      <a href="#">About Us</a>
      <a href="#">Services</a>
      <a href="#">Pathology Consultants</a>
      <a href="#">Patients</a>
      <a href="#">Results</a>
      <a href="#">Accounts</a>
      <a href="#">Contact Us</a>
    </nav>
  </header>

  <div class="rule" style="top:132px"></div>
  <p class="intro-quote">"Lorem ipsum dolor sit amet, consectetur adipisicing elit, sed do eiusmod tempor incididunt ut labore et dolore magna aliqua. Ut enim ad minim veniam, quis nostrud exercitation ullamco laboris nisi ut aliquip ex ea commodo consequat.</p>
  <div class="rule" style="top:291px"></div>

  <section class="hero" role="img" aria-label="Photo of two pathologists in lab coats working at a laboratory bench">
    <div class="hero-dots"><i class="active"></i><i></i><i></i></div>
  </section>

  <div class="tabs">
    <div class="tab active">Pathology</div>
    <div class="tab">Treatments</div>
  </div>

  <article class="article col-left">
    <h2>Childhood Disease</h2>
    <p class="lead" style="margin-top:14px">Cum sociis natoque penatibus et quis dis ent montes, cetur ridiculus ulla dui. Fusce feugiatmalesu.</p>
    <p style="margin-top:16px">Morbi unc odio, gravida at, cursus nec, luctus a, lorem. Maecenaique orci ac sem. Duis ultricies pharetra magna. Donec cumsan malesuada orci. Donec sit amet eroorem ipsum dolor sit amet, consectetuer adipiscing elit. Mauris fermentumcuis ultricies pharetra magna</p>
    <div class="divider-dotted" style="margin-top:37px"></div>
    <p style="margin-top:29px">Fusce feugiatmalesuada odio. Morbi unc odio, gravida at, cursus nec, luctus a, lorem. Maecenaique orci ac sem. Duis ultricies pharetra magna. <span class="inline-link">Donec cumsan malesuada</span> orci. Donec sit amet eros. Lorem ipsum dolor sit amet, consectetuer adipiscing elit. Mauris fermentumcuis ultricies pharetra magna orci. Donec sit amet eros. Lorem ipsum dolor sit amet, consectetuer adipiscing elit.</p>
    <a class="more" href="#" style="margin-top:15px">more info</a>
    <div class="divider-solid" style="margin-top:16px"></div>
  </article>

  <article class="article col-mid">
    <div class="article-photo" role="img" aria-label="Photo of a scientist looking into a laboratory microscope"></div>
    <h2 style="margin-top:18px">DNA Using Microscope</h2>
    <p style="margin-top:10px"><span class="strong-link">Lorem ipsum dolor set amet</span> Atmalesuada odio. Morbi unc odio, gravida at, cursus nec, luctus a, lorem. Maecenaique orci ac sem. Duis ultricies pharetra magna. Donec</p>
    <p style="margin-top:15px"><span class="strong-link">Fusce feugiatmalesuada odio.</span> Morbi unc odio, gravida at, cursus nec, luctus a, lorem. Maecenaique orci ac sem. Duis ultricies pharetra magna. Donec accumsan male</p>
    <a class="more" href="#" style="margin-top:15px">more info</a>
    <div class="divider-solid" style="margin-top:17px"></div>
  </article>

  <aside class="sidebar">
    <h3>Our Services</h3>
    <ul class="service-list">
      <li><svg viewBox="0 0 14 14"><circle cx="7" cy="7" r="7" fill="#bdbdbd"/><path d="M5.5 4 L9.5 7 L5.5 10 Z" fill="#fff"/></svg>Autopsy Pathology</li>
      <li><svg viewBox="0 0 14 14"><circle cx="7" cy="7" r="7" fill="#bdbdbd"/><path d="M5.5 4 L9.5 7 L5.5 10 Z" fill="#fff"/></svg>Bone and Soft Tissue Pathology</li>
      <li><svg viewBox="0 0 14 14"><circle cx="7" cy="7" r="7" fill="#bdbdbd"/><path d="M5.5 4 L9.5 7 L5.5 10 Z" fill="#fff"/></svg>Clinically Interactive Consultative</li>
      <li><svg viewBox="0 0 14 14"><circle cx="7" cy="7" r="7" fill="#bdbdbd"/><path d="M5.5 4 L9.5 7 L5.5 10 Z" fill="#fff"/></svg>Dermatopathology</li>
      <li><svg viewBox="0 0 14 14"><circle cx="7" cy="7" r="7" fill="#bdbdbd"/><path d="M5.5 4 L9.5 7 L5.5 10 Z" fill="#fff"/></svg>Forensic Pathology</li>
      <li><svg viewBox="0 0 14 14"><circle cx="7" cy="7" r="7" fill="#bdbdbd"/><path d="M5.5 4 L9.5 7 L5.5 10 Z" fill="#fff"/></svg>Gastrointestinal &amp; Hepatic</li>
      <li><svg viewBox="0 0 14 14"><circle cx="7" cy="7" r="7" fill="#bdbdbd"/><path d="M5.5 4 L9.5 7 L5.5 10 Z" fill="#fff"/></svg>Hematology &amp; Hemato</li>
      <li><svg viewBox="0 0 14 14"><circle cx="7" cy="7" r="7" fill="#bdbdbd"/><path d="M5.5 4 L9.5 7 L5.5 10 Z" fill="#fff"/></svg>Immunopathology/Histopathology</li>
      <li><svg viewBox="0 0 14 14"><circle cx="7" cy="7" r="7" fill="#bdbdbd"/><path d="M5.5 4 L9.5 7 L5.5 10 Z" fill="#fff"/></svg>Pediatric Pathology</li>
      <li><svg viewBox="0 0 14 14"><circle cx="7" cy="7" r="7" fill="#bdbdbd"/><path d="M5.5 4 L9.5 7 L5.5 10 Z" fill="#fff"/></svg>Surgical Pathology</li>
      <li><svg viewBox="0 0 14 14"><circle cx="7" cy="7" r="7" fill="#bdbdbd"/><path d="M5.5 4 L9.5 7 L5.5 10 Z" fill="#fff"/></svg>Urologic Pathology</li>
    </ul>
    <a class="btn btn-dark" href="#">See Our Test Menu</a>
    <a class="btn btn-blue" href="#">Speak with one of the<br>Pathologists</a>
  </aside>

  <footer class="site-footer">
    <p class="copyright">Copyright © 2013 Consultants, Inc . All Rights Reserved</p>
    <div class="social">
      <i style="background:#f08a1c"></i>
      <i style="background:#6e9a3c"></i>
      <i style="background:#45b0e3"></i>
      <i style="background:#2f86d6"></i>
    </div>
  </footer>
</body>
</html>
```